New Service Brochure for The Brellford Spa

Hi All! We are looking for a new brochure design- tri-fold, double sided, and full color. We are a certified Tallow Spa for men and women in the heart of the Catskill Mountains of upstate New York. Our clients would describe us as laid back luxury with no pretensions and a home away from home vibe. Our font is Avalon. Key colors are black, white and gold. Looking for an inviting, clean, and modern/minimalist spread with a touch of elegance. No orchid imagery, please. I would like our "Tallow Spa" logo on cover, too please. Front cover image with with logo and "Tallow Spa" Sticker . Bottom of back with contact info. We would prefer massages go on left inside page, facials in middle and right inside, nails on back left, but we are open to new or different layout proposals. Thank you!

Target Market(s)

Men & Women.

Industry/Entity Type

Health And Wellness

Other font styles liked:
• Avalon is our signature font

Requirements
Must have
• Easy on the eyes.
Nice to have
• Negative space.
Should not have
• No orchids. Busy lines and wild colors.

```html
<!DOCTYPE html>
<html lang="en">
<head>
<meta charset="utf-8">
<title>The Brellford Spa – Service Brochure</title>
<link rel="stylesheet" href="https://fonts.googleapis.com/css2?family=Raleway:wght@300;400;500&display=swap">
<style>
:root{
  --page:#e4e4e6;
  --ink:#1b1a1b;
  --dark-1:#3d3c3d;
  --dark-2:#141314;
  --gold:#c9a257;
  --gold-soft:#e3cb95;
  --band:#d9bd7e;
  --white:#ffffff;
  --body-dark:#4a4440;
  --muted:#6b6661;
}
*{margin:0;padding:0;box-sizing:border-box}
html,body{width:787px;height:1200px;overflow:hidden;background:var(--page)}
body{position:relative;font-family:"Raleway",Arial,sans-serif;color:var(--white)}

.sheet{position:absolute;left:52px;width:656px;height:505px;display:grid;
  grid-template-columns:219px 218px 219px;box-shadow:0 10px 10px -6px rgba(0,0,0,.28)}
.sheet--outside{top:59px;grid-template-rows:138px 4px 277px 6px 80px}
.sheet--inside{top:603px;grid-template-rows:374px 5px 126px}

.band{grid-column:1 / 4;background:linear-gradient(90deg,var(--band),var(--gold-soft),var(--band))}
.panel{position:relative;overflow:hidden}
.panel--dark{background:radial-gradient(ellipse at 50% 35%,var(--dark-1),var(--dark-2) 80%)}
.panel--black{background:linear-gradient(180deg,#2e2d2e,var(--dark-2))}
.panel--light{background:var(--white);color:var(--ink)}
.photo{width:100%;height:100%}

.wordmark{font-weight:300;color:var(--white);text-transform:uppercase;text-align:center;letter-spacing:.04em;line-height:1.05}
.tagline{color:var(--gold);font-size:8.4px;text-align:center;font-weight:400;letter-spacing:.02em}

.svc{margin-bottom:8px}
.svc-head{display:flex;align-items:baseline;font-size:6.3px;color:var(--gold);line-height:1.2}
.svc-head .lead{flex:1;border-bottom:1px dotted currentColor;margin:0 2px;transform:translateY(-1px)}
.svc-desc{font-size:4.9px;line-height:1.35;margin-top:1px}

.heading{font-weight:400;font-size:12px;letter-spacing:.02em}

/* outside */
.hands{padding:44px 9px 0 7px}
.hands .heading{color:var(--gold);margin-bottom:10px}
.hands p.intro{font-size:6.6px;line-height:1.32;color:var(--gold);text-align:justify}
.partner{position:absolute;top:14px;right:10px;display:flex;align-items:center;gap:3px}
.partner-box{width:20px;height:22px;background:var(--gold)}
.partner-name{font-size:4.6px;color:var(--ink);line-height:1.2;width:34px;text-transform:uppercase}

.cover-top{display:flex;flex-direction:column;align-items:center;justify-content:center;gap:8px}
.cover-top .wordmark{font-size:25px}

.nails{padding:10px 8px 0 7px}
.nails .svc{margin-bottom:9px}

.contact{display:flex;flex-direction:column;align-items:center;padding-top:30px}
.contact .wordmark{font-size:25px;margin-bottom:8px}
.btn{margin-top:20px;background:var(--gold);color:var(--white);font-size:8.6px;padding:5px 12px;letter-spacing:.02em}
.contact-lines{margin-top:22px;text-align:center;font-size:8.5px;line-height:1.55}
.contact-lines .gap{margin-bottom:6px}

.badge{position:absolute;right:3px;bottom:6px;width:58px;height:58px}

.hours{text-align:center;color:var(--muted);font-size:8.3px;line-height:1.75;padding-top:11px}
.escape{text-align:center;padding-top:20px}
.escape p{font-size:11.5px;line-height:1.5;font-weight:300}
.escape .web{font-size:8.6px;color:var(--gold);margin-top:6px;font-weight:400}

/* inside – explicit placement */
.massages{grid-column:1;grid-row:1;padding:30px 8px 0 8px}
.massages .heading{margin-bottom:10px}
.massages .intro{font-size:6.8px;line-height:1.2;color:var(--gold);margin-bottom:9px}
.massages .svc{margin-bottom:8px}

.facials{grid-column:2;grid-row:1 / 4;background:var(--white);color:var(--ink)}
.facials .photo{height:125px}
.facials-body{padding:10px 9px 0 11px}
.facials .heading{color:var(--gold);margin-bottom:5px}
.facials .intro{font-size:6.6px;line-height:1.2;color:var(--gold);margin-bottom:11px}
.facials .svc{margin-bottom:9px}
.facials .svc-desc{color:var(--body-dark)}

.hair{grid-column:3;grid-row:1;padding:33px 10px 0 12px}
.hair .heading{margin-bottom:9px}
.sub{font-size:6.3px;color:var(--gold);text-transform:uppercase;margin-bottom:1px}
.hair .note{font-size:6.6px;line-height:1.2;color:var(--gold);margin-bottom:5px}
.price-list{font-size:6.8px;line-height:1.72;list-style:none}
.price-list span,.wax span{color:var(--gold)}
.waxing{margin-top:26px}
.wax{display:grid;grid-template-columns:1fr 1fr;font-size:6.8px;line-height:1.72;list-style:none;margin-top:6px}

.band--left{grid-column:1;grid-row:2}
.band--right{grid-column:3;grid-row:2}
.photo-cell--left{grid-column:1;grid-row:3}
.photo-cell--right{grid-column:3;grid-row:3}
</style>
</head>
<body>

<section class="sheet sheet--outside" aria-label="Brochure outside">
  <div class="panel panel--light hands">
    <div class="partner"><span class="partner-box"></span><span class="partner-name">Verlaine Botanics</span></div>
    <h2 class="heading">Hands &amp; feet</h2>
    <p class="intro">Melt into a Pedicure Throne in our Nail Lounge. Our handmade soaks and scrubs are made in house with only the freshest natural and organic ingredients! Your hands and feet have never been loved like this! All nail services include nail and cuticle care, massage and polish of choice.</p>
  </div>
  <div class="panel"><div class="photo" role="img" aria-label="Bright nail lounge with marble pedicure tub" style="background:linear-gradient(160deg,#f6e3c8,#e9c9a0 55%,#fbf2e6)"></div></div>
  <div class="panel panel--black cover-top">
    <h1 class="wordmark">The Brellford<br>Spa</h1>
    <p class="tagline">a boutique spa for Men &amp; Women</p>
  </div>

  <div class="band"></div>

  <div class="panel panel--dark nails">
    <div class="svc"><p class="svc-head"><span>Organic Eight Greens Manicure</span><span class="lead"></span><span>$65</span></p><p class="svc-desc">Hydrate, smooth and clarify tired and abused hands. Stone crop cleansing oil, eight greens exfoliant and lotus detox hand treatment. 55 minutes.</p></div>
    <div class="svc"><p class="svc-head"><span>Hot Stone Manicure</span><span class="lead"></span><span>$65</span></p><p class="svc-desc">Heal and smooth tired hands with our signature keratin and copaiba hot herbal mitts. 55 minutes.</p></div>
    <div class="svc"><p class="svc-head"><span>Reverse The Hands Of Time Manicure</span><span class="lead"></span><span>$75</span></p><p class="svc-desc">The name says it all. Smoothing lava scrub, brightening masque, and luscious tightening hand creme. 55 minutes.</p></div>
    <div class="svc"><p class="svc-head"><span>Palo Santo Pedicure</span><span class="lead"></span><span>$85</span></p><p class="svc-desc">Includes our bespoke bergamot and balsam foot soak, refreshing peppermint scrub, and Palo Santo lotion. 55 minutes.</p></div>
    <div class="svc"><p class="svc-head"><span>Brellford Spa Pedicure</span><span class="lead"></span><span>$75</span></p><p class="svc-desc">In addition to a classic pedicure, a soothing anti-inflammatory mud mask, paraffin wrap treatment and revitalizing foot massage. Topped off with your choice of enamel. 55 minutes.</p></div>
    <div class="svc"><p class="svc-head"><span>Mother of Dragonfruit Pedicure</span><span class="lead"></span><span>$85</span></p><p class="svc-desc">Breaker of calluses, reliever of tired feet, queen of the cuticle, mother of spring cleaning and perfectly polished toes. Soak, scrub, cuticle and nail care. Hot stone foot and leg massage. Polish. 55 minutes.</p></div>
    <div class="svc"><p class="svc-head"><span>Grapefruit and Pine Pedicure</span><span class="lead"></span><span>$45</span></p><p class="svc-desc">A perfect pick me up for any feet that want to celebrate the season! Soak. Scrub. Cuticle &amp; nail care. Polish. Boom. 30 minutes.</p></div>
  </div>
  <div class="panel panel--dark contact">
    <p class="wordmark">The Brellford<br>Spa</p>
    <p class="tagline">a boutique spa for Men &amp; Women</p>
    <span class="btn">GET IN TOUCH</span>
    <div class="contact-lines">
      <p class="gap">(555) 014-2236</p>
      <p class="gap">Info@TheBrellfordSpa.com</p>
      <p>42 Alder Hollow Road</p>
      <p>Brellford, NY 12000</p>
      <p>Just off Main Street!</p>
    </div>
  </div>
  <div class="panel">
    <div class="photo" role="img" aria-label="Guest relaxing on a massage table with rolled towels" style="background:radial-gradient(ellipse at 40% 45%,#e3bc8e,#a8774c 60%,#5e3e26)"></div>
    <svg class="badge" viewBox="0 0 58 58" role="img" aria-label="Tallow Spa certification badge"><circle cx="29" cy="29" r="27" fill="#5a9a3a"/><circle cx="29" cy="29" r="21" fill="none" stroke="#3f7a28" stroke-width="2"/></svg>
  </div>

  <div class="band"></div>

  <div class="panel"><div class="photo" role="img" aria-label="Pedicure being given in a white soaking basin" style="background:linear-gradient(150deg,#3a3130,#c9b3a2 55%,#f1ece7)"></div></div>
  <div class="panel panel--light hours">
    <p>HOURS</p>
    <p>Thurs-Sat: 10am-6pm</p>
    <p>Sun-Mon: 10am-5pm</p>
    <p>Tues &amp; Wed: Closed</p>
  </div>
  <div class="panel panel--black escape">
    <p>ESCAPE THE CONGESTION OF<br>EVERYDAY LIFE!</p>
    <p class="web">www.thebrellfordspa.com</p>
  </div>
</section>

<section class="sheet sheet--inside" aria-label="Brochure inside">
  <div class="panel panel--dark massages">
    <h2 class="heading">Massages</h2>
    <p class="intro">Tired, sore muscles, and exhausted minds are refreshed by the perfect massage customized to your individual needs.</p>
    <div class="svc"><p class="svc-head"><span>Swedish Massage</span><span class="lead"></span><span>$105/$160</span></p><p class="svc-desc">Relaxing and therapeutic. Ease tension and enhance circulation. Great for a first time massage or any spa veteran. 55min - 90min</p></div>
    <div class="svc"><p class="svc-head"><span>Deep Tissue</span><span class="lead"></span><span>$115/$175</span></p><p class="svc-desc">A therapeutic combination of slow and deep pressure alleviates chronic pain, muscle fatigue, and limited range of motion. Muscle therapy lotion or creme. 55min - 90min</p></div>
    <div class="svc"><p class="svc-head"><span>Tension Tamer</span><span class="lead"></span><span>$125/$195</span></p><p class="svc-desc">Head, neck and shoulders. Deep tissue with hot towels, muscle soothing oils, and cupping. 55min - 90min</p></div>
    <div class="svc"><p class="svc-head"><span>Hot Stone</span><span class="lead"></span><span>$175</span></p><p class="svc-desc">Unforgettable. Warm basalt lava stones melt away all stress and tension in sore muscles and joints. The ultimate après ski treat. 90min</p></div>
    <div class="svc"><p class="svc-head"><span>Recovery</span><span class="lead"></span><span>$110/$170</span></p><p class="svc-desc">Specific to your athletic needs, whether pro or a weekend warrior. Relax, stretch, and recover. 55min - 90min</p></div>
    <div class="svc"><p class="svc-head"><span>Kinetra Rapid Recovery Massage</span><span class="lead"></span><span>$135</span></p><p class="svc-desc">Ideal for runners, cyclists, hikers, skiers &amp; riders. Recover faster and feel better with Kinetra compression chamber sleeves. Mobilize fluid &amp; speed recovery for tired, sore and aching legs. Includes head, neck, shoulders, arm and hand massage. 55 minutes.</p></div>
    <div class="svc"><p class="svc-head"><span>Prenatal</span><span class="lead"></span><span>$110</span></p><p class="svc-desc">Ultimate treat for mother-to-be. Soothes aches and pains during pregnancy. Mother must be out of first trimester. 55 minutes.</p></div>
    <div class="svc"><p class="svc-head"><span>Couples</span><span class="lead"></span><span>$210 &amp; up</span></p><p class="svc-desc">For lovebirds or loved ones. Relax and recoup with your favorite person. 55 or 90 minutes.</p></div>
  </div>

  <div class="panel facials">
    <div class="photo" role="img" aria-label="Woman with glowing skin after a facial" style="background:linear-gradient(170deg,#f7f2ee,#efd9c6 50%,#f8f4f0)"></div>
    <div class="facials-body">
      <h2 class="heading">Facials</h2>
      <p class="intro">Featuring Verlaine Botanics products our organic and biodynamic facials are perfect for even the most sensitive skin!</p>
      <div class="svc"><p class="svc-head"><span>Detox Facial</span><span class="lead"></span><span>$135</span></p><p class="svc-desc">Increases oxygen and blood flow to dramatically reboot your skin's natural healing abilities and reveal healthier skin. 55 minutes.</p></div>
      <div class="svc"><p class="svc-head"><span>B.L.T. Facial</span><span class="lead"></span><span>$145</span></p><p class="svc-desc">Organic triple peel, also known as our "Runway Peel" because it leaves you glowing and ready for the red carpet immediately. 55 minutes.</p></div>
      <div class="svc"><p class="svc-head"><span>Double Down Facial</span><span class="lead"></span><span>$165</span></p><p class="svc-desc">Organic triple peel, also known as our "Runway Peel" because it leaves you glowing and ready for the red carpet immediately. 55 minutes.</p></div>
      <div class="svc"><p class="svc-head"><span>Organic Masque Montage</span><span class="lead"></span><span>$115</span></p><p class="svc-desc">Three layers of customized masques created exclusively for your skin type. Includes steam, cleanse, exfoliation, extractions, masques, massage, and moisturizer. 55 minutes.</p></div>
      <div class="svc"><p class="svc-head"><span>Calm Skin Facial</span><span class="lead"></span><span>$125</span></p><p class="svc-desc">Combat redness, irritation and dryness. Gentle, yet effective for even the most sensitive skin types. Soothe, hydrate, and refresh. 55 mins</p></div>
      <div class="svc"><p class="svc-head"><span>R&amp;R Facial</span><span class="lead"></span><span>$255 (Reg. $275)</span></p><p class="svc-desc">Our most dynamic results oriented facial, and the ultimate kick start to rebooting skin after a long summer of sunshine and heat. Microdermabrasion, double peel, LED light. 90 minutes.</p></div>
      <div class="svc"><p class="svc-head"><span>Mangosteen Facial</span><span class="lead"></span><span>$135</span></p><p class="svc-desc">Minimize pore size and surface build up with zero down time. Our organic lactic acid peel leaves skin smooth, clarified and glowing! 55 minutes.</p></div>
      <div class="svc"><p class="svc-head"><span>Microdermabrasion</span><span class="lead"></span><span>$115</span></p><p class="svc-desc">Reduce wrinkles, scarring, discoloration, sun damage, large pores and age spots. Stimulate collagen and elastin production. Best in series of six. 30min.</p></div>
    </div>
  </div>

  <div class="panel panel--dark hair">
    <h2 class="heading">Hair Removal</h2>
    <p class="sub">Electrolysis</p>
    <p class="note">Say goodbye to unwanted and embarrassing hair with the only FDA approved method of Permanent Hair Removal. Great for men and women of all ages.</p>
    <ul class="price-list">
      <li>15 Minutes - <span>$25</span></li>
      <li>30 Minutes - <span>$45</span></li>
      <li>45 Minutes - <span>$60</span></li>
      <li>60 Minutes - <span>$75</span></li>
      <li>4 Hour Bonus Pack - <span>$240</span></li>
    </ul>
    <div class="waxing">
      <p class="sub">Waxing</p>
      <p class="note">Using only the best wax in the world, our custom blends of French and domestic waxes make for a flawless waxing experience. From eyebrows to Brazilians, your comfort and care is our priority.</p>
      <ul class="wax">
        <li>Lips - <span>$12</span></li><li>Brazilian - <span>$65+</span></li>
        <li>Chin - <span>$12</span></li><li>Chest - <span>$30+</span></li>
        <li>Eyebrows - <span>$15</span></li><li>Back - <span>$35+</span></li>
        <li>Sideburns - <span>$20</span></li><li>Underarm - <span>$28</span></li>
        <li>Lower Half Leg - <span>$30</span></li><li>Half Arm - <span>$25</span></li>
        <li>Upper Half Leg - <span>$40</span></li><li>Full Arm - <span>$38</span></li>
        <li>Full Leg - <span>$65</span></li><li>Feet - <span>$10</span></li>
        <li>Bikini (top &amp; sides) - <span>$50</span></li><li>Hands - <span>$8</span></li>
      </ul>
    </div>
  </div>

  <div class="band band--left"></div>
  <div class="band band--right"></div>

  <div class="panel photo-cell--left"><div class="photo" role="img" aria-label="Friends celebrating a spa party with treats" style="background:linear-gradient(120deg,#f3e6dd,#e5c7b1 45%,#f6efe8)"></div></div>
  <div class="panel photo-cell--right"><div class="photo" role="img" aria-label="Hot stone massage on a guest's back" style="background:linear-gradient(150deg,#6b4a36,#d2a57d 50%,#f0dcc7)"></div></div>
</section>

</body>
</html>
```